Government contracting small business needs a web design

Tarvex Summit Inc is a veteran owned small business that delivers a full range of professional services as well as training in information technology, security and defense intelligence solutions.
We need a professional/corporate looking website where potential clients can view what services are offered.
This being a new company, there is not much that can added more than a narrative statement, stock photos and a place where potential customers and employees can make contact.
Open to ideas.
Target Market(s)
US Government
Industry/Entity Type
Small Business
Look and feel
Each slider illustrates characteristics of the customer's brand and the style your logo design should communicate.

```html
<!DOCTYPE html>
<html lang="en">
<head>
<meta charset="utf-8">
<title>Tarvex Summit Inc</title>
<link href="https://fonts.googleapis.com/css2?family=PT+Sans:wght@400;700&family=PT+Sans+Narrow:wght@400;700&family=Roboto+Condensed:wght@700&family=Kalam:wght@400&display=swap" rel="stylesheet">
<style>
  :root {
    --yellow: #f2c21b;
    --yellow-dark: #d9aa10;
    --ink: #111111;
    --panel: #525252;
    --panel-field: #3f3f3f;
    --text-dark: #4a4a4a;
    --muted: #c9ccd2;
    --footer-bg: #ebebeb;
    --white: #ffffff;
    --track: #e4e5e8;
  }
  * { margin: 0; padding: 0; box-sizing: border-box; }
  html, body { width: 925px; height: 1200px; overflow: hidden; }
  body { position: relative; background: var(--white); font-family: "PT Sans", Arial, sans-serif; color: var(--ink); }
  .abs { position: absolute; }

  .brand { left: 20px; top: 24px; display: flex; align-items: center; gap: 6px; }
  .brand-mark { width: 34px; height: 34px; border-radius: 50%; background: var(--ink); }
  .brand-name { font-family: "PT Sans", Arial, sans-serif; font-weight: 700; font-size: 22px; letter-spacing: -0.3px; }

  .search { left: 694px; top: 31px; width: 211px; height: 22px; border: 1px solid #dcdcdc; border-radius: 4px;
    background: linear-gradient(#f3f3f3, #fdfdfd); }
  .search svg { position: absolute; right: 9px; top: 5px; }

  .main-nav { left: 9px; top: 68px; width: 905px; height: 38px; background: var(--yellow);
    border: 1px solid var(--yellow-dark); box-shadow: inset 0 0 0 2px #f7d550; }
  .main-nav a { position: absolute; top: 14px; font-family: Arial, sans-serif; font-weight: 700; font-size: 10px;
    color: var(--ink); text-decoration: none; }
  .main-nav .sep { position: absolute; top: 2px; width: 1px; height: 32px; background: var(--yellow-dark); }

  .hero { left: 9px; top: 114px; width: 905px; height: 310px; }
  .hero-photo { width: 100%; height: 100%;
    background: radial-gradient(ellipse at 55% 40%, #fff6c8 0%, #ffd766 30%, #f8a640 62%, #e5553a 100%); }
  .hero-title { left: 508px; top: 88px; font-family: "Roboto Condensed", "Arial Narrow", sans-serif; font-weight: 700;
    font-size: 52px; line-height: 46px; color: var(--ink); letter-spacing: -0.5px; }
  .hero-lead { left: 514px; top: 193px; width: 340px; font-family: Arial, sans-serif; font-weight: 700; font-size: 12px; line-height: 15px; }

  .steps { left: 9px; top: 428px; width: 905px; height: 70px; }
  .steps .track { position: absolute; left: 0; top: 12px; width: 905px; height: 5px; background: var(--track); border-radius: 3px; }
  .steps .knob { position: absolute; top: 0; width: 30px; height: 30px; border-radius: 50%; background: #f1f2f4;
    border: 1px solid #dfe0e3; }
  .steps .knob.active::after { content: ""; position: absolute; left: 7px; top: 7px; width: 14px; height: 14px; border-radius: 50%;
    background: radial-gradient(circle at 40% 35%, #ffe25a, #e9ad08); }
  .steps .label { position: absolute; top: 44px; width: 140px; text-align: center; font-family: "PT Sans Narrow", sans-serif;
    font-size: 15px; color: var(--muted); }
  .steps .label.active { color: var(--text-dark); }

  .info-panel { left: 9px; top: 515px; width: 905px; height: 332px; background: var(--panel); border: 2px solid #dedede; color: var(--white); }
  .info-panel h2 { position: absolute; font-family: "PT Sans Narrow", sans-serif; font-weight: 400; font-size: 20px; }
  .feature-title { position: absolute; width: 310px; font-family: "PT Sans Narrow", sans-serif; font-weight: 700; font-size: 15px; line-height: 19px; }
  .feature-body { position: absolute; width: 310px; font-size: 9.5px; line-height: 12px; }
  .news-date { position: absolute; font-family: "Kalam", cursive; font-size: 15px; color: var(--yellow); }
  .news-body { position: absolute; width: 210px; font-size: 10px; line-height: 13px; }
  .btn { position: absolute; height: 27px; background: var(--yellow); color: var(--white); font-family: "PT Sans Narrow", sans-serif;
    font-size: 11px; text-align: center; line-height: 28px; text-transform: uppercase; }
  .signup-lead { position: absolute; left: 611px; top: 72px; width: 270px; font-family: "PT Sans Narrow", sans-serif; font-weight: 700;
    font-size: 11.5px; line-height: 14px; }
  .field { position: absolute; left: 614px; width: 219px; height: 29px; background: var(--panel-field);
    box-shadow: inset 0 2px 4px rgba(0,0,0,.45); font-size: 9px; line-height: 27px; padding-left: 17px; }

  .intro h3 { position: absolute; font-family: "PT Sans Narrow", sans-serif; font-weight: 700; color: var(--text-dark); }
  .intro p { position: absolute; font-size: 10.5px; line-height: 13px; color: var(--ink); }

  .site-footer { left: 0; top: 1060px; width: 925px; height: 140px; background: var(--footer-bg); }
  .footer-col { position: absolute; top: 32px; }
  .footer-col h4 { font-size: 13px; font-weight: 700; color: #3a3a3a; margin-bottom: 6px; }
  .footer-col a { display: block; font-size: 11px; color: #3a3a3a; text-decoration: none; line-height: 22px; }
  .copyright { position: absolute; left: 617px; top: 99px; font-size: 11px; color: var(--ink); }
</style>
</head>
<body>

<header>
  <div class="brand abs"><span class="brand-mark"></span><span class="brand-name">Tarvex Summit</span></div>
  <div class="search abs">
    <svg width="12" height="12" viewBox="0 0 12 12"><circle cx="5" cy="5" r="3.3" fill="none" stroke="#222" stroke-width="1.6"/><line x1="7.5" y1="7.5" x2="11" y2="11" stroke="#222" stroke-width="2"/></svg>
  </div>
  <nav class="main-nav abs">
    <a style="left:30px">HOME</a><span class="sep" style="left:81px"></span>
    <a style="left:100px">INNOVATION</a><span class="sep" style="left:180px"></span>
    <a style="left:199px">OUR COMPANY</a><span class="sep" style="left:292px"></span>
    <a style="left:312px">INVESTORS</a><span class="sep" style="left:384px"></span>
    <a style="left:406px">SERVICES</a><span class="sep" style="left:470px"></span>
    <a style="left:494px">NEWSROOM</a><span class="sep" style="left:572px"></span>
    <a style="left:593px">CAREERS</a><span class="sep" style="left:662px"></span>
    <a style="left:678px">CONTACT</a>
  </nav>
</header>

<section class="hero abs">
  <div class="hero-photo" role="img" aria-label="Silhouette of a soldier holding a rifle against a glowing orange sunset sky"></div>
  <h1 class="hero-title abs">Powerful &amp;<br>effective</h1>
  <p class="hero-lead abs">Praesent vestibulum molestie lacus. Aenean nonummy hendrerit mauris. Phasellus porta. Fusce suscipit varius mi.</p>
</section>

<div class="steps abs">
  <div class="track"></div>
  <span class="knob" style="left:66px"></span>
  <span class="knob" style="left:309px"></span>
  <span class="knob" style="left:553px"></span>
  <span class="knob active" style="left:789px"></span>
  <span class="label" style="left:12px">EXPERIENCE</span>
  <span class="label" style="left:254px">SOLUTIONS</span>
  <span class="label" style="left:498px">STRATEGIES</span>
  <span class="label active" style="left:728px">SUCCESS</span>
</div>

<section class="info-panel abs">
  <h2 style="left:29px;top:26px">FEATURED</h2>
  <p class="feature-title" style="left:29px;top:69px">Phasellus porta. Fusce suscipit varius mi. Cum sociis natoque penatibus et magnis dis parturient montes.</p>
  <p class="feature-body" style="left:29px;top:119px">Nascetur ridiculus mus. Nulla dui. Fusce feugiat malesuada odio. Morbi nunc odio, gravida at, cursus nec, luctus a, lorem. Maecenas tristique orci ac sem. Duis ultricies pharetra magna.</p>
  <p class="feature-title" style="left:29px;top:178px">Phasellus porta. Fusce suscipit varius mi. Cum sociis natoque penatibus et magnis dis parturient montes.</p>
  <p class="feature-body" style="left:29px;top:228px">Nascetur ridiculus mus. Nulla dui. Fusce feugiat malesuada odio. Morbi nunc odio, gravida at, cursus nec, luctus a, lorem. Maecenas tristique orci ac sem. Duis ultricies pharetra magna.</p>
  <span class="btn" style="left:227px;top:284px;width:98px">Read more</span>

  <h2 style="left:372px;top:26px">NEWS &amp; EVENTS</h2>
  <span class="news-date" style="left:372px;top:71px">Jun 19, 2012</span>
  <p class="news-body" style="left:372px;top:97px">Phasellus porta. Fusce suscipit varius mi. Cum sociis natoque penatibus et magnis dis parturient montes, nascetur.</p>
  <span class="news-date" style="left:372px;top:180px">Jun 19, 2012</span>
  <p class="news-body" style="left:372px;top:205px">Phasellus porta. Fusce suscipit varius mi. Cum sociis natoque penatibus et magnis dis parturient montes, nascetur.</p>
  <span class="btn" style="left:471px;top:284px;width:98px">Read more</span>

  <h2 style="left:608px;top:26px">NEWSLETTER SIGN UP</h2>
  <p class="signup-lead">Phasellus porta. Fusce suscipit varius mi. Cum sociis natoque penatibus et magnis dis parturient montes.</p>
  <div class="field" style="top:115px">your name</div>
  <div class="field" style="top:151px">email id</div>
  <div class="field" style="top:187px">phone number</div>
  <span class="btn" style="left:733px;top:229px;width:98px">Sign up!</span>
</section>

<section class="intro">
  <h3 style="left:22px;top:878px;font-size:21px">Welcome</h3>
  <p style="left:22px;top:916px;width:410px">Phasellus porta. Fusce suscipit varius mi. Cum sociis natoque penatibus et magnis dis parturient montes, nascetur ridiculus mus. Nulla dui. Fusce feugiat malesuada odio. Morbi nunc odio, gravida at, cursus nec, luctus a, lorem.<br>Maecenas tristique orci ac sem. Duis ultricies pharetra magna.<br><br>Donec accumsan maada orci. Donec sit amet eros. Lorem ipsum dolor sit amet, consectetuer adipiscing elit.</p>
  <h3 style="left:457px;top:890px;font-size:21px">Our work is dedicated to the prosperity of our clients!</h3>
  <p style="left:457px;top:929px;width:448px">Phasellus porta. Fusce suscipit varius mi. Cum sociis natoque penatibus et magnis dis parturient montes, nascetur ridiculus mus. Nulla dui. Fusce feugiat malesuada odio. Morbi nunc odio, gravida at, cursus nec, luctus a, lorem. Maecenas tristique orci ac sem. Duis ultricies pharetra magna.<br><br>Donec accumsan maada orci. Donec sit amet eros. Lorem ipsum dolor sit amet, consectetuer adipiscing elit.</p>
</section>

<footer class="site-footer abs">
  <div class="footer-col" style="left:34px"><h4>About us</h4><a>Who we are</a><a>Our people</a><a>Careers</a></div>
  <div class="footer-col" style="left:133px"><h4>About us</h4><a>Who we are</a><a>Our people</a><a>Careers</a></div>
  <div class="footer-col" style="left:223px"><h4>About us</h4><a>Who we are</a><a>Our people</a><a>Careers</a></div>
  <div class="footer-col" style="left:314px"><h4>About us</h4><a>Who we are</a><a>Our people</a><a>Careers</a></div>
  <div class="footer-col" style="left:404px"><h4>About us</h4><a>Who we are</a><a>Our people</a><a>Careers</a></div>
  <div class="footer-col" style="left:494px"><h4>About us</h4><a>Who we are</a><a>Our people</a><a>Careers</a></div>
  <p class="copyright">Tarvex Summit © 2012 | Privacy Policy</p>
</footer>

</body>
</html>
```